Braek down, maintainance and support for satelite and TV

I want a website designed for a satellite engineer firm i want it to look modern. I am finalizing the content with the underwriters at the moment so format we can start on the format and pictures. I want it to be easy to navigate with some eye capturing imiges. I am currently waiting for the underwriters to get the contact over so if we can start on everything else. I ONLY ADDED THE SCREEN SHOT AS I HAD TO ADD SOMETHING TO CONTINUE PLEASE USE YOUR OWN IDEAS

Target Market(s)

Every one

Industry/Entity Type

Tv

Number of Pages Required

5+ page

Font styles to use
Sans Serif

```html
<!DOCTYPE html>
<html lang="en">
<head>
<meta charset="utf-8">
<title>Satellite Engineering Firm</title>
<link rel="stylesheet" href="https://fonts.googleapis.com/css2?family=Source+Sans+3:wght@400;600;700&display=swap">
<style>
:root{
  --teal:#4a8fae;
  --teal-dark:#3a7594;
  --navy:#2c5870;
  --ink:#222;
  --grey-text:#555;
  --frame:#e6e6e6;
  --footer:#333;
  --white:#fff;
}
*{box-sizing:border-box;margin:0;padding:0}
html,body{width:1200px;height:2880px;overflow:hidden}
body{background:var(--frame);font-family:"Source Sans 3",Arial,sans-serif;color:var(--ink)}
.page{position:absolute;left:15px;top:15px;width:1170px;height:2850px;background:var(--white);overflow:hidden}
section,header,nav,footer{position:absolute;left:0;width:1170px}

/* header */
.site-header{top:0;height:139px}
.brand{position:absolute;left:30px;top:40px;display:flex;align-items:center;gap:16px}
.brand-dot{width:60px;height:60px;border-radius:50%;background:var(--teal)}
.brand-name{font-size:28px;font-weight:700;color:var(--teal);line-height:1.05}
.callout{position:absolute;right:30px;top:38px;display:flex;align-items:center;gap:12px}
.callout-label{font-size:18px;font-weight:700;color:var(--teal);line-height:1}
.callout-number{font-size:34px;font-weight:600;color:#333;line-height:1.05}

/* nav */
.main-nav{top:141px;height:42px;background:var(--teal);display:flex;padding-left:44px}
.main-nav a{display:block;height:42px;line-height:42px;padding:0 28px;color:var(--white);font-size:17px;font-weight:700;text-decoration:none;text-transform:uppercase}
.main-nav a.is-active{background:var(--navy)}

/* hero */
.hero{top:183px;height:551px;background:linear-gradient(180deg,#6f9fc9 0%,#a9c6df 45%,#dfe8ef 75%,#c9b9a4 100%)}
.welcome{top:734px;height:199px;background:var(--teal);text-align:center;color:var(--white);padding-top:20px}
.welcome h1{font-size:34px;font-weight:700;letter-spacing:.3px;line-height:1.2}
.welcome p{font-size:15.5px;font-weight:600;width:1100px;margin:8px auto 0;line-height:1.5}
.welcome-actions{display:flex;justify-content:center;gap:20px;margin-top:14px}
.btn-outline{width:330px;height:42px;border:2px solid var(--white);border-radius:8px;font-size:19px;font-weight:600;line-height:38px}
.btn-outline.dark{background:var(--navy);color:var(--white)}
.btn-outline.light{background:var(--white);color:#333}

/* what we do */
.services{top:933px;height:565px;text-align:center}
.section-title{font-size:26px;font-weight:700;color:var(--teal);text-transform:uppercase}
.services .section-title{margin-top:40px}
.services p.intro{width:1060px;margin:20px auto 0;font-size:15.5px;font-weight:600;line-height:1.5}
.service-list{display:flex;justify-content:center;gap:0;margin-top:26px;list-style:none}
.service-list li{width:180px;font-size:16.5px;font-weight:600;color:var(--grey-text);line-height:1.4;display:flex;flex-direction:column;align-items:center}
.service-icon{width:140px;height:140px;border-radius:50%;border:3px solid var(--teal);background:#f1f1f1;display:flex;align-items:center;justify-content:center;margin-bottom:18px}
.btn-dark{display:inline-flex;align-items:center;justify-content:space-between;width:200px;height:40px;border-radius:8px;background:#333;color:var(--white);font-size:17px;font-weight:700;padding:0 8px 0 22px;text-transform:uppercase}
.btn-dark .arrow{width:38px;height:32px;border-radius:6px;background:#666;display:flex;align-items:center;justify-content:center}
.services .btn-dark{margin-top:24px}

/* testimonials */
.testimonials{top:1485px;height:343px;background:linear-gradient(120deg,#6ea0bd,#4f8aab 50%,#6a9fbd);color:var(--white)}
.testimonials .section-title{color:var(--white);text-align:center;margin-top:34px}
.quote-row{display:flex;gap:58px;padding:0 28px 0 37px;margin-top:26px}
.quote{width:540px;display:flex;gap:12px}
.quote-mark{font-size:70px;font-weight:700;line-height:.8;height:40px;flex:none}
.quote-close{display:inline-block;font-size:60px;font-weight:700;line-height:0;vertical-align:-22px;margin-left:14px}
.quote p{font-size:15.5px;line-height:1.45}
.quote cite{display:block;font-style:normal;font-weight:700;font-size:16px;margin-top:24px;line-height:1.45}
.dots{position:absolute;left:0;right:0;top:300px;display:flex;justify-content:center;gap:6px}
.dots span{width:11px;height:11px;border-radius:50%;border:1.5px solid var(--white)}
.dots span.on{background:var(--white)}

/* careers */
.careers{top:1828px;height:307px}
.careers .section-title{position:absolute;left:67px;top:40px}
.careers p{position:absolute;left:67px;top:90px;width:600px;font-size:16.5px;font-weight:600;line-height:1.5}
.careers .btn-dark{position:absolute;left:65px;top:235px}
.careers-photo{position:absolute;right:0;top:0;width:495px;height:307px;background:linear-gradient(160deg,#f4f4f4,#c9ccd0 50%,#3a3d44)}

/* news and blog */
.updates{top:2135px;height:465px;background:linear-gradient(180deg,var(--teal-dark),#4a86a5 60%,#5a93b0)}
.updates h2{position:absolute;top:34px;font-size:27px;font-weight:700;color:var(--white);text-transform:uppercase}
.news-item{position:absolute;left:65px;width:430px;display:flex;gap:16px;color:var(--white)}
.news-thumb{width:102px;height:102px;border-radius:50%;border:4px solid var(--white);flex:none;background:linear-gradient(180deg,#6d96bf,#b7cde0 60%,#555)}
.news-item h3{font-size:13px;font-weight:700}
.news-item p{font-size:13.5px;line-height:1.3;width:240px}
.pill{display:block;width:180px;height:28px;border-radius:8px;background:#333;color:var(--white);text-align:center;line-height:28px;font-size:13px;font-weight:700;margin-top:8px}
.blog-card{position:absolute;top:110px;width:268px;height:330px;background:var(--white);border:4px solid #ddd;box-shadow:0 2px 6px rgba(0,0,0,.3)}
.blog-thumb{height:183px}
.blog-thumb.tech{background:linear-gradient(135deg,#0a1a3a,#2d5ea0 50%,#dfe6ee)}
.blog-thumb.puzzle{background:linear-gradient(135deg,#6fb5c6,#2a6b80 60%,#0e3040)}
.blog-card h3{font-size:14px;font-weight:700;margin:14px 0 0 12px}
.blog-card p{font-size:14px;line-height:1.3;margin:2px 12px 0}
.blog-card .btn-teal{display:block;width:178px;height:44px;margin:14px auto 0;background:var(--teal);color:var(--white);text-align:center;line-height:44px;font-weight:700;font-size:15px;border-radius:3px}

/* footer */
.site-footer{top:2600px;height:250px;background:var(--footer);color:var(--white)}
.footer-wedge{position:absolute;right:0;top:0}
.footer-col{position:absolute;top:32px}
.footer-col h4{font-size:16px;font-weight:700;color:var(--teal);text-transform:uppercase;margin-bottom:22px}
.footer-col li{list-style:none;font-size:13.5px;font-weight:700;line-height:19px;text-transform:uppercase}
.contact-line{display:flex;gap:12px;font-size:13.5px;font-weight:700;line-height:19px;margin-bottom:18px}
.contact-line .email{text-transform:none}
.social li{display:flex;align-items:center;gap:14px;margin-bottom:22px}
.social .mark{width:22px;height:22px;border-radius:50%;background:var(--white)}
.footer-mark{position:absolute;right:50px;top:80px;width:90px;height:90px;border-radius:50%;background:var(--teal)}
</style>
</head>
<body>
<div class="page">

  <header class="site-header">
    <div class="brand">
      <span class="brand-dot"></span>
      <span class="brand-name">Satellite<br>Engineering Firm</span>
    </div>
    <div class="callout">
      <svg width="48" height="48" viewBox="0 0 48 48"><circle cx="24" cy="24" r="22" fill="none" stroke="#4a8fae" stroke-width="3"/><path d="M16 13c2-1 4 4 4 6s-3 2-2 4 5 7 7 7 2-3 4-2 6 3 5 5-3 3-6 2-15-10-14-17z" fill="#4a8fae"/></svg>
      <div><div class="callout-label">CALL US TODAY</div><div class="callout-number">202-555-0143</div></div>
    </div>
  </header>

  <nav class="main-nav">
    <a class="is-active">Home</a><a>Who We Are</a><a>What We Do</a><a>What Clients Say</a><a>Careers</a><a>News</a><a>Blog</a><a>Contact</a>
  </nav>

  <section class="hero" role="img" aria-label="Row of large satellite dishes against a blue cloudy sky"></section>

  <section class="welcome">
    <h1>WELCOME TO SATELLITE ENGINEERING FIRM</h1>
    <p>Lorem ipsum dolor sit amet, consectetuer adipiscing elit, sed diam nonummy nibh euismod tincidunt ut laoreet dolore magna aliquam erat volutpat. Ut wisi enim ad minim veniam, quis nostrud exerci tation ullamcorper suscipit lobortis nisl ut aliquip ex ea commodo consequat.</p>
    <div class="welcome-actions">
      <span class="btn-outline dark">LEARN MORE ABOUT US</span>
      <span class="btn-outline light">CONTACT US NOW</span>
    </div>
  </section>

  <section class="services">
    <h2 class="section-title">What We Do</h2>
    <p class="intro">Lorem ipsum dolor sit amet, consectetuer adipiscing elit, sed diam nonummy nibh euismod tincidunt ut laoreet dolore magna aliquam erat volutpat. Ut wisi enim ad minim veniam, quis nostrud exerci tation ullamcorper suscipit lobortis nisl ut aliquip ex ea commodo consequat. Duis autem vel eum iriure dolor in hendrerit in vulputate velit esse molestie consequat, vel illum dolore eu feugiat nulla facilisis at vero eros et accumsan et iusto odio dignissim qui blandit praesent luptatum zzril delenit augue duis dolore te feugait nulla facilisi.</p>
    <ul class="service-list">
      <li><div class="service-icon"><svg width="76" height="76" viewBox="0 0 76 76" fill="none" stroke="#4a8fae" stroke-width="4"><circle cx="38" cy="38" r="14"/><circle cx="38" cy="38" r="24" stroke-dasharray="8 6"/><path d="M22 58l16-16"/></svg></div>System Engineering</li>
      <li><div class="service-icon"><svg width="76" height="76" viewBox="0 0 76 76" fill="none" stroke="#4a8fae" stroke-width="4"><rect x="18" y="14" width="40" height="52" rx="4"/><rect x="30" y="9" width="16" height="10" rx="2"/><circle cx="38" cy="42" r="10"/><path d="M38 40v8M38 36v1"/></svg></div>Site Surveying</li>
      <li><div class="service-icon"><svg width="76" height="76" viewBox="0 0 76 76" fill="#4a8fae"><path d="M14 30a28 28 0 0 0 34 26z"/><path d="M30 44l16-16" stroke="#4a8fae" stroke-width="4"/><circle cx="48" cy="26" r="4"/><path d="M26 52l-6 16h24l-6-14z"/></svg></div>Ground stations<br>Installation<br>and Maintenance</li>
      <li><div class="service-icon"><svg width="76" height="76" viewBox="0 0 76 76" fill="none" stroke="#4a8fae" stroke-width="4"><circle cx="38" cy="38" r="24"/><ellipse cx="38" cy="38" rx="11" ry="24"/><path d="M14 38h48M18 26h40M18 50h40"/></svg></div>Worldwide Data<br>Telecommunication<br>&amp; Installation</li>
      <li><div class="service-icon"><svg width="76" height="76" viewBox="0 0 76 76" fill="none" stroke="#4a8fae" stroke-width="6" stroke-linecap="round"><path d="M12 32a37 37 0 0 1 52 0M21 41a24 24 0 0 1 34 0"/><circle cx="38" cy="52" r="5" fill="#4a8fae" stroke="none"/></svg></div>Wireless<br>LAN Networks</li>
      <li><div class="service-icon"><svg width="76" height="76" viewBox="0 0 76 76" fill="none" stroke="#4a8fae" stroke-width="4"><circle cx="38" cy="18" r="7"/><circle cx="18" cy="44" r="7"/><circle cx="58" cy="44" r="7"/><path d="M33 23l-10 15M43 23l10 15M25 44h26"/></svg></div>Component &amp;<br>Systems Analysis</li>
    </ul>
    <span class="btn-dark">Learn More <span class="arrow"><svg width="16" height="16" viewBox="0 0 16 16" fill="none" stroke="#fff" stroke-width="2"><path d="M2 8h11M9 4l4 4-4 4"/></svg></span></span>
  </section>

  <section class="testimonials" role="img" aria-label="Blue toned background of business people talking in an office">
    <h2 class="section-title">What Clients Say</h2>
    <div class="quote-row">
      <div class="quote"><span class="quote-mark">&ldquo;</span><div><p>Lorem ipsum dolor sit amet, consectetuer adipiscing elit, sed diam nonummy nibh euismod tincidunt ut laoreet dolore magna aliquam erat volutpat. Ut wisi enim ad minim veniam, quis nostrud exerci tation ullamcorper suscipit lobortis nisl ut aliquip.<span class="quote-close">&rdquo;</span></p><cite>Marisa Holt<br>Company A</cite></div></div>
      <div class="quote"><span class="quote-mark">&ldquo;</span><div><p>Lorem ipsum dolor sit amet, consectetuer adipiscing elit, sed diam nonummy nibh euismod tincidunt ut laoreet dolore magna aliquam erat volutpat. Ut wisi enim ad minim veniam, quis nostrud exerci tation ullamcorper suscipit lobortis nisl ut aliquip.<span class="quote-close">&rdquo;</span></p><cite>Daniel Orwin<br>Company B</cite></div></div>
    </div>
    <div class="dots"><span class="on"></span><span></span><span></span><span></span></div>
  </section>

  <section class="careers">
    <h2 class="section-title">Careers</h2>
    <p>Lorem ipsum dolor sit amet, consectetuer adipiscing elit, sed diam nonummy nibh euismod tincidunt ut laoreet dolore magna aliquam erat volutpat. Ut wisi enim ad minim veniam, quis nostrud exerci tation ullamcorper suscipit lobortis nisl ut aliquip ex ea commodo consequat. Duis autem vel eum iriure dolor in hendrerit in vulputate velit esse molestie consequat.</p>
    <span class="btn-dark">Learn More <span class="arrow"><svg width="16" height="16" viewBox="0 0 16 16" fill="none" stroke="#fff" stroke-width="2"><path d="M2 8h11M9 4l4 4-4 4"/></svg></span></span>
    <div class="careers-photo" role="img" aria-label="Group of four smiling business professionals in suits"></div>
  </section>

  <section class="updates" role="img" aria-label="Faint satellite and solar panel artwork on a blue background">
    <h2 style="left:73px">Latest News</h2>
    <h2 style="left:560px">Blog</h2>
    <div class="news-item" style="top:92px"><div class="news-thumb" role="img" aria-label="Satellite dish under a blue sky"></div><div><h3>NEWS#1</h3><p>Lorem ipsum dolor sit amet, consectetuer adipiscing elit, sed diam nonummy nibh euismod tincidunt ut laoreet dolore.</p><span class="pill">READ MORE</span></div></div>
    <div class="news-item" style="top:242px"><div class="news-thumb" role="img" aria-label="Large antenna dish at a ground station"></div><div><h3>NEWS#2</h3><p>Lorem ipsum dolor sit amet, consectetuer adipiscing elit, sed diam nonummy nibh euismod tincidunt ut laoreet dolore.</p><span class="pill">READ MORE</span></div></div>
    <article class="blog-card" style="left:557px"><div class="blog-thumb tech" role="img" aria-label="Glowing digital gears with a person in a shirt"></div><h3>Blog #1</h3><p>Lorem ipsum dolor sit amet, consec tetuer adipiscing elit, sed diam.</p><span class="btn-teal">READ MORE</span></article>
    <article class="blog-card" style="left:836px"><div class="blog-thumb puzzle" role="img" aria-label="Blue puzzle pieces with one piece lifted"></div><h3>Blog #2</h3><p>Lorem ipsum dolor sit amet, consec tetuer adipiscing elit, sed diam.</p><span class="btn-teal">READ MORE</span></article>
  </section>

  <footer class="site-footer">
    <svg class="footer-wedge" width="240" height="250" viewBox="0 0 240 250"><path d="M30 0H240V250H0Z" fill="#fff"/></svg>
    <div class="footer-col" style="left:43px"><h4>Menu</h4><ul><li>Who We Are</li><li>What We Do</li><li>What Clients Say</li><li>Careers</li><li>News</li><li>Blog</li><li>Contact</li></ul></div>
    <div class="footer-col" style="left:235px"><h4>What We Do</h4><ul><li>System Engineering</li><li>Site Surveying</li><li>Ground Station Installation</li><li>Telecommunication</li><li>LAN Network</li><li>Component &amp; System Analysis</li></ul></div>
    <div class="footer-col" style="left:528px"><h4>Contact Info</h4>
      <div class="contact-line"><svg width="14" height="20" viewBox="0 0 14 20"><path d="M7 0a7 7 0 0 1 7 7c0 5-7 13-7 13S0 12 0 7a7 7 0 0 1 7-7z" fill="#fff"/><circle cx="7" cy="7" r="2.5" fill="#333"/></svg><span>48 ORBIT LANE<br>UNIT #48<br>VALENCIA, SPAIN</span></div>
      <div class="contact-line"><svg width="18" height="16" viewBox="0 0 18 16"><path d="M1 4c0-3 16-3 16 0v3h-5V5H6v2H1zM3 9h12l2 7H1z" fill="#fff"/></svg><span>202-555-0143</span></div>
      <div class="contact-line"><svg width="18" height="14" viewBox="0 0 18 14"><rect width="18" height="14" fill="#fff"/><path d="M1 1l8 7 8-7" fill="none" stroke="#333" stroke-width="1.5"/></svg><span class="email">info@skyreachfirm.com</span></div>
    </div>
    <div class="footer-col social" style="left:765px"><h4>Follow Us</h4><ul><li><span class="mark"></span>Circlepage</li><li><span class="mark"></span>Chirpline</li><li><span class="mark"></span>Workweb</li></ul></div>
    <div class="footer-mark"></div>
  </footer>

</div>
</body>
</html>
```